Musical download and streaming website

hello designers, I want to start up a musical website where users can download and rate music of different genres such as RnB, Hip hop, rock, afro-pop. This website should be attractive and contemporary. There will be a search column for different songs. Music files will be mp3, mwa, and others. I like blue, gold, pink and indigo colors. My website should resemble http://tunovalt.com. There should be good imaginary of music stars on my website.

```html
<!DOCTYPE html>
<html lang="en">
<head>
<meta charset="utf-8">
<title>Corvane Sound</title>
<link href="https://fonts.googleapis.com/css2?family=Cinzel:wght@400;600;700&family=Open+Sans:wght@400;600;700&display=swap" rel="stylesheet">
<style>
:root{
  --gold:#b38f22;
  --gold-light:#c9a536;
  --gold-panel:#b08c1c;
  --ink:#0f0f10;
  --songs-bg:#141414;
  --white:#ffffff;
  --line:#2f2f2f;
  --nav-red:#c0262c;
}
*{margin:0;padding:0;box-sizing:border-box}
html,body{width:1200px;height:2594px;overflow:hidden}
body{position:relative;background:var(--ink);font-family:"Open Sans",Arial,sans-serif;color:var(--white)}
.abs{position:absolute}
.heading{font-family:"Cinzel",Georgia,serif;font-weight:600;letter-spacing:1px}

/* hero */
.hero{left:0;top:0;width:1200px;height:614px;
  background:radial-gradient(ellipse at 50% 95%,#2a2fb8 0%,#1b1870 30%,transparent 60%),
  linear-gradient(180deg,#1d1424 0%,#21182c 40%,#1a1550 75%,#120e3a 100%)}
.brand{left:112px;top:68px;font-family:"Cinzel",Georgia,serif;font-weight:700;font-size:34px;line-height:44px;color:var(--white);letter-spacing:1px;white-space:nowrap}
.nav{left:590px;top:70px}
.nav a{color:var(--white);text-decoration:none;font-weight:700;font-size:12px;text-transform:uppercase;position:absolute;top:4px;white-space:nowrap}
.hero-title{left:0;width:1200px;top:296px;text-align:center;font-size:45px;color:var(--white)}
.socials{left:463px;top:375px;display:flex;gap:9px}
.social{width:48px;height:48px;border:2px solid rgba(255,255,255,.75);border-radius:50%}
.dots{left:1142px;top:255px;display:flex;flex-direction:column;gap:17px}
.dots span{width:9px;height:9px;border-radius:50%;background:var(--white)}
.dots span:first-child{background:transparent;border:1.5px solid var(--white)}

/* welcome */
.welcome{left:0;top:614px;width:1200px;height:442px;
  background:radial-gradient(ellipse at 80% 80%,#3a2c2a 0%,transparent 45%),
  radial-gradient(ellipse at 25% 30%,#2a1838 0%,transparent 50%),
  linear-gradient(180deg,#1a1020 0%,#1c1222 100%)}
.welcome h2{position:absolute;left:0;width:1200px;top:148px;text-align:center;font-size:35px;color:var(--gold)}
.welcome p{position:absolute;left:262px;width:676px;top:205px;text-align:center;font-size:13.5px;line-height:24px;color:#e6e6e6}
.play{left:560px;top:333px}

/* artists */
.artists-head{left:0;top:1056px;width:1200px;height:121px;background:#141212}
.artists-head h2{position:absolute;width:1200px;top:44px;text-align:center;font-size:35px;color:var(--gold)}
.tile{position:absolute}
.panel{background:var(--gold-panel);text-align:center;color:var(--white)}
.panel h3{font-size:20px;font-weight:700;margin-top:60px}
.panel p{font-size:11.5px;line-height:17px;margin:6px auto 0;width:190px}
.panel .pill{display:inline-block;margin-top:16px;border:1.5px solid var(--white);border-radius:16px;padding:5px 18px;font-size:10px;font-weight:700}

/* songs */
.songs{left:0;top:1630px;width:1200px;height:396px;background:var(--songs-bg)}
.songs h2{position:absolute;left:107px;top:52px;font-size:36px;line-height:48px;color:var(--gold)}
.song-row{position:absolute;left:100px;width:609px;height:70px;border-bottom:1px solid var(--line);font-size:14px;color:#e2e2e2}
.song-row span{position:absolute;top:24px;line-height:19px}
.btn{position:absolute;top:18px;height:31px;width:104px;font-size:13px;text-align:center;line-height:29px;border:1px solid var(--gold);color:var(--gold)}
.btn.filled{background:linear-gradient(180deg,var(--gold-light),#9c7a18);color:var(--white)}
.view-rate{left:90px;top:326px;width:133px;height:44px;border-radius:22px;background:var(--gold);font-size:13px;line-height:44px;text-align:center;color:var(--white)}
.snap{position:absolute;border:4px solid var(--white)}

/* contact */
.contact{left:0;top:2026px;width:1200px;height:568px;
  background:radial-gradient(ellipse at 75% 40%,#1a3a48 0%,transparent 55%),
  radial-gradient(ellipse at 15% 70%,#142a36 0%,transparent 50%),
  linear-gradient(180deg,#0d1a22 0%,#0e1c24 60%,#0b141a 100%)}
.contact h2{position:absolute;width:1200px;top:62px;text-align:center;font-size:36px;color:var(--white)}
.field{position:absolute;left:102px;width:401px;background:var(--white);border-radius:2px;color:#6b6b6b;font-size:11px;font-weight:600;padding-left:36px;line-height:40px}
.field svg{position:absolute;left:13px;top:13px}
.submit{left:99px;top:2453px;width:172px;height:47px;border-radius:24px;background:var(--gold);font-size:14px;font-weight:700;line-height:47px;text-align:center}
.info{position:absolute;left:576px;font-size:12px;color:#e0e0e0;line-height:19px}
.info svg{position:absolute;left:0;top:2px}
.info span{display:block;margin-left:26px}
.footer-copy{left:104px;top:2557px;font-size:13px;color:#dcdcdc}
.foot-social{left:935px;top:2552px;display:flex;gap:6px}
.foot-social span{width:29px;height:29px;border:1.5px solid #dcdcdc;border-radius:50%}
.footer-code{left:1139px;top:2558px;font-size:11px;color:#dcdcdc}
</style>
</head>
<body>

<header class="abs hero" role="img" aria-label="Photo of a night club crowd behind a DJ mixing desk in blue light"></header>
<div class="abs brand">CORVANE SOUND</div>
<nav class="abs nav">
  <svg class="abs" style="left:0;top:0" width="18" height="16" viewBox="0 0 18 16"><path d="M9 1 L1 8 H3.5 V15 H7.5 V10.5 H10.5 V15 H14.5 V8 H17 Z" fill="var(--nav-red)"/></svg>
  <a style="left:64px">About</a>
  <a style="left:152px">Download Music</a>
  <a style="left:318px">List of Music</a>
  <a style="left:453px">Contact</a>
</nav>
<h1 class="abs heading hero-title">CORVANE SOUND</h1>
<div class="abs socials"><span class="social"></span><span class="social"></span><span class="social"></span><span class="social"></span><span class="social"></span></div>
<div class="abs dots"><span></span><span></span><span></span><span></span><span></span></div>

<section class="abs welcome" role="img" aria-label="Dim photo of a DJ booth with turntables">
  <h2 class="heading">WELCOME TO&nbsp; CORVANE SOUND</h2>
  <p>Lorem Ipsum is simply dummy text of the printing and typesetting industry. Lorem Ipsum has been the industry's standard dummy text ever since the 1500s, when an unknown printer took a galley of type and scrambled it to make a type specimen book. It has survived not only five centuries, but also the leap into electronic typesetting, remaining essentially unchanged.</p>
  <svg class="abs play" width="80" height="80" viewBox="0 0 80 80"><circle cx="40" cy="40" r="38" fill="none" stroke="var(--gold)" stroke-width="2"/><path d="M33 28 L53 40 L33 52 Z" fill="var(--gold)"/></svg>
</section>

<section class="abs artists-head"><h2 class="heading">TOP ARTISTS</h2></section>
<div class="tile" style="left:0;top:1177px;width:240px;height:227px;background:linear-gradient(135deg,#1a2aa8,#3540d8 50%,#161460)" role="img" aria-label="DJ performing under blue stage lights"></div>
<div class="tile" style="left:240px;top:1177px;width:479px;height:453px;background:radial-gradient(ellipse at 55% 25%,#ffe27a 0%,#f0a020 30%,#b04a30 60%,#2a1840 100%)" role="img" aria-label="Crowd raising hands under golden concert lights"></div>
<div class="tile" style="left:719px;top:1177px;width:241px;height:227px;background:radial-gradient(ellipse at 50% 30%,#a8e8ff 0%,#2a6ad0 35%,#0c1030 80%)" role="img" aria-label="Concert crowd under bright white and blue lights"></div>
<div class="tile panel" style="left:960px;top:1177px;width:240px;height:227px">
  <h3>LOREM IPSUM</h3><p>LOREM IPSUM IS SIMPLY DUMMY TEXT OF THE PRINTING...</p><span class="pill">VIEW INFO</span>
</div>
<div class="tile panel" style="left:0;top:1404px;width:240px;height:226px">
  <h3>LOREM IPSUM</h3><p>LOREM IPSUM IS SIMPLY DUMMY TEXT OF THE PRINTING...</p><span class="pill">VIEW INFO</span>
</div>
<div class="tile" style="left:719px;top:1404px;width:241px;height:226px;background:linear-gradient(150deg,#7a2ab8,#d040b0 45%,#30104a)" role="img" aria-label="DJ turntable lit in pink and violet"></div>
<div class="tile" style="left:960px;top:1404px;width:240px;height:226px;background:linear-gradient(160deg,#3a3ac8,#6a5ae0 45%,#141250)" role="img" aria-label="Headphones resting on a mixing desk in blue light"></div>

<section class="abs songs">
  <h2 class="heading">TOP SONGS</h2>
  <div class="song-row" style="top:93px"><span style="left:0">01</span><span style="left:54px">RnB</span><span style="left:287px">04.12</span><a class="btn filled" style="left:386px">Paused</a><a class="btn filled" style="left:500px">Download</a></div>
  <div class="song-row" style="top:163px"><span style="left:0">02</span><span style="left:58px">Hip hop</span><span style="left:287px">03.17</span><a class="btn" style="left:386px">Paused</a><a class="btn" style="left:500px">Download</a></div>
  <div class="song-row" style="top:233px"><span style="left:0">03</span><span style="left:58px">Rock</span><span style="left:287px">02.12</span><a class="btn" style="left:386px">Paused</a><a class="btn" style="left:500px">Download</a></div>
  <div class="abs view-rate">VIEW RATE</div>
  <div class="snap" style="left:778px;top:33px;width:142px;height:140px;transform:rotate(-2deg);background:linear-gradient(135deg,#c89a30,#6a4a20)" role="img" aria-label="Hands on a DJ controller"></div>
  <div class="snap" style="left:921px;top:47px;width:146px;height:138px;transform:rotate(2deg);background:linear-gradient(135deg,#5a4aa0,#2a2060)" role="img" aria-label="DJ mixer close up"></div>
  <div class="snap" style="left:787px;top:177px;width:141px;height:138px;transform:rotate(1deg);background:linear-gradient(135deg,#2a6ad0,#0e1a40)" role="img" aria-label="DJ on stage in blue light"></div>
  <div class="snap" style="left:930px;top:185px;width:147px;height:146px;transform:rotate(-2deg);background:linear-gradient(135deg,#7ad87a,#1e5a40)" role="img" aria-label="DJ at a mixing deck in green light"></div>
</section>

<section class="abs contact" role="img" aria-label="Dark teal photo of a DJ at the decks">
  <h2 class="heading">CONTACT US</h2>
</section>
<div class="field" style="top:2163px;height:41px"><svg width="12" height="13" viewBox="0 0 12 13"><circle cx="6" cy="3.5" r="3" fill="#555"/><path d="M0 13 C0 8 12 8 12 13 Z" fill="#555"/></svg>YOUR NAME</div>
<div class="field" style="top:2222px;height:40px"><svg width="14" height="11" viewBox="0 0 14 11"><rect width="14" height="11" rx="1" fill="#555"/><path d="M0 1 L7 6 L14 1" stroke="#fff" fill="none"/></svg>EMAIL ADDRESS</div>
<div class="field" style="top:2279px;height:40px"><svg width="11" height="13" viewBox="0 0 11 13"><path d="M0 0 H7 L11 4 V13 H0 Z" fill="#555"/><path d="M2 7 H9 M2 10 H9" stroke="#fff"/></svg>SUBJECT</div>
<div class="field" style="top:2336px;height:102px;line-height:30px"><svg style="top:9px" width="12" height="12" viewBox="0 0 12 12"><path d="M0 12 L1 8 L9 0 L12 3 L4 11 Z" fill="#555"/></svg>MESSAGE</div>
<div class="abs submit">SUBMIT</div>

<div class="abs brand" style="left:562px;top:2178px">CORVANE SOUND</div>
<div class="info" style="top:2290px"><svg width="12" height="17" viewBox="0 0 12 17"><path d="M6 0 C2.7 0 0 2.6 0 6 C0 10 6 17 6 17 C6 17 12 10 12 6 C12 2.6 9.3 0 6 0 Z" fill="#fff"/><circle cx="6" cy="6" r="2.3" fill="#0e1c24"/></svg><span>Lorem Ipsum is simply dummy<br>text setting street-395001</span></div>
<div class="info" style="top:2338px;font-size:14px"><svg width="14" height="14" viewBox="0 0 14 14"><path d="M3 0 L5.5 3.5 L4 5.5 C5 7.5 6.5 9 8.5 10 L10.5 8.5 L14 11 L12 14 C6 14 0 8 0 2 Z" fill="#fff"/></svg><span>+1 555 014 2290</span></div>
<div class="info" style="top:2378px;font-size:11px"><svg width="15" height="11" viewBox="0 0 15 11"><rect width="15" height="11" fill="#fff"/><path d="M0 0 L7.5 6 L15 0" stroke="#0e1c24" fill="none"/></svg><span>hello@corvanesound.example</span></div>

<div class="abs footer-copy">Copyright © 2016 Allrights reserved</div>
<div class="abs foot-social"><span></span><span></span><span></span><span></span><span></span></div>
<div class="abs footer-code">C12</div>

</body>
</html>
```